Retail Sign for Houseplant Campaign

Sign will measure 3 to 4 foot tall by 22.2inches and place on rolling racks of houseplants for a retail promotion in The Birchwell Yard. The theme of the promotion will be "New Year, New You!" Selling points which should be on the sign are Houseplants give you a taste of nature, Houseplants boost air quality inside your home, Indoor plants reduce anxiety, Indoor plants make you more productive, Houseplants improve your concentration and memory.
Updates

Target Market(s)

People who love plants

Industry/Entity Type

Horticulture/ retail

Colors
00AB8E
00BBA5
67D7C9
C6EFE9
E9F9F6
59FF00
82FF00
B8FF75
E3FFCB
F4FFEA
FFF300
FFF600
FEFA6F
FFFEC7
FFFEE8

Requirements
Must have
• Must feel energetic and encourage people to buy plants. Should include 1-2 photos and the selling points listed

```html
<!DOCTYPE html>
<html lang="en">
<head>
<meta charset="utf-8">
<title>New Year, New You! – Houseplant Sign</title>
<link rel="stylesheet" href="https://fonts.googleapis.com/css2?family=Kaushan+Script&family=Comic+Neue:wght@400;700&family=Arimo:wght@400&display=swap">
<style>
  :root {
    --page: #ffffff;
    --sun: #fff23f;
    --ink: #231f20;
    --lagoon: #67d7c9;
    --leaf-lime: #c8dc45;
    --leaf-green: #7fb244;
    --dot-green: #5ffd3a;
    --dot-lime: #bdfc75;
    --photo-wall: #eef0ee;
    --photo-warm: #d9c2a8;
  }
  * { margin: 0; padding: 0; box-sizing: border-box; }
  html, body {
    width: 668px; height: 1200px; overflow: hidden;
    background: var(--page);
  }
  .sign {
    position: absolute;
    left: 97px; top: 90px;
    width: 471px; height: 1027px;
    background: var(--sun);
    overflow: hidden;
  }
  .leaf { position: absolute; }
  .leaf--left { left: 0; top: 0; width: 182px; height: 172px; }
  .leaf--right { left: 380px; top: 0; width: 91px; height: 104px; }

  .brand {
    position: absolute;
    left: 124px; top: 50px; width: 222px; height: 44px;
    display: flex; align-items: center; gap: 10px;
  }
  .brand__mark {
    width: 40px; height: 40px; background: var(--ink); flex: none;
  }
  .brand__name {
    font-family: "Arimo", Arial, sans-serif;
    font-weight: 400; font-size: 27px; letter-spacing: 0.5px;
    color: var(--ink); white-space: nowrap; line-height: 1;
  }

  .headline {
    position: absolute; left: 0; top: 116px; width: 100%;
    text-align: center;
    font-family: "Kaushan Script", cursive;
    font-weight: 400; font-size: 54px; line-height: 66px;
    color: var(--ink);
  }

  .benefits {
    position: absolute; left: 40px; top: 262px; width: 391px;
    list-style: none; text-align: center;
    font-family: "Comic Neue", cursive;
    font-weight: 400; font-size: 22px; line-height: 30px;
    color: var(--ink);
  }
  .benefits li + li { margin-top: 8px; }

  .photo-frame { position: absolute; left: 0; top: 0; width: 471px; height: 1027px; }
  .wave { position: absolute; left: 0; top: 0; width: 471px; height: 1027px; }
</style>
</head>
<body>
  <main class="sign">
    <svg class="leaf leaf--left" viewBox="0 0 182 172" role="img" aria-label="Lime-tinted monstera leaf">
      <path d="M0 0 H150 C178 30 186 90 170 125 C150 165 100 175 60 160 C30 148 10 130 0 110 Z" fill="var(--leaf-lime)"/>
    </svg>
    <svg class="leaf leaf--right" viewBox="0 0 91 104" role="img" aria-label="Green monstera leaf">
      <path d="M91 0 V100 C60 108 20 100 5 75 C-5 50 15 15 40 0 Z" fill="var(--leaf-green)"/>
    </svg>

    <div class="brand">
      <span class="brand__mark"></span>
      <span class="brand__name">Verdant Hollow</span>
    </div>

    <h1 class="headline">New Year,<br>New You!</h1>

    <ul class="benefits">
      <li>Houseplants give you a<br>taste of nature</li>
      <li>Houseplants boost air quality<br>inside your home</li>
      <li>Indoor plants reduce anxiety</li>
      <li>Indoor plants make you<br>more productive</li>
      <li>Houseplants improve your<br>concentration and memory</li>
    </ul>

    <svg class="wave" viewBox="0 0 471 1027" aria-hidden="true">
      <path d="M0 935 C30 918 60 908 90 910 C160 914 230 975 300 1002 C340 1016 380 988 420 988 C445 988 462 1002 471 1015 V1027 H0 Z" fill="var(--lagoon)"/>
    </svg>

    <svg class="photo-frame" viewBox="0 0 471 1027">
      <circle cx="230" cy="760" r="176" fill="none" stroke="var(--ink)" stroke-width="0.8"/>
      <circle cx="230" cy="760" r="163" fill="var(--photo-wall)" role="img" aria-label="Photo of a smiling woman placing a potted croton plant on a shelf"/>
      <ellipse cx="280" cy="800" rx="80" ry="120" fill="var(--photo-warm)" opacity="0.5"/>
      <circle cx="373" cy="656" r="24" fill="var(--dot-green)"/>
      <circle cx="83" cy="849" r="24" fill="var(--dot-lime)"/>
    </svg>
  </main>
</body>
</html>
```